Business Card - high end, modern health care

Hey designers!

We need a double sided business card for the boutique, cutting edge physical therapy rehabilitation centre in Sydney's Northern Beaches.

With the most qualified physios in the area The Harbourview Motion Clinic does what other physiotherapy practices do not, we take our time with our patients giving them longer appointments, better physios and therefor faster results!

We guarantee that the service people receive at THMC will be unparalleled.

Hence we need a business card to reflect our modern, boutique, high end service. The final design needs to reflect that we are in a class of our own yet with the feel of beachside retreat.

Below I have attached our logo in both blue on white and white on blue. The exact colour is;
and the font that we have used in our logo is Tex Gyre Aventador.

I like the idea of the blue as the main colour as it is more eye catching and our signage onto the main road will be in this blue and in the interest of consistency across marketing the blue needs to be a part of the design. However I would appreciate a few designs onto a wooden background as this is a visual theme within the fitout of the practice.

The design needs to be of standard size (91x55mm).

Target Market(s)

We target people who have an end outcome in mind and those who have had poor experiences with other providers and ensure that everyone gets the care that they deserve with a premium service that is tailored to the individuals circumstances. As a premium service, the target market is highly educated, business and tech savvy with the additional target market of elderly people who have self funded their retirement and see value in paying for the best ongoing rehabilitation to maintain independence.

Industry/Entity Type

Physical Therapy

Contact Information for Business Card

Name, designation( Titled Musculoskeletal Physiotherapist... there will also be those in the company that have multiple designations ie 5 or 6 words long), phone number, email, facebook, instagram, address

Font styles to use
Sans Serif

Colors

Designer to choose colors to be used in the design.

Requirements
Must have
• Front - The logo as large as possible, blue or wooden theme, and all of the important details.
• Back - A blank space/lines on which to write appointment times (no "Appointment, date, time" etc.)
Nice to have
• facebook url
• logos for facebook and instagram
• Mini logos for the phone and email?

```html
<!DOCTYPE html>
<html lang="en">
<head>
<meta charset="utf-8">
<title>The Harbourview Motion Clinic – Business Card</title>
<link href="https://fonts.googleapis.com/css2?family=Lato:wght@400;700;900&display=swap" rel="stylesheet">
<style>
  :root {
    --brand-blue: #1d4fa8;
    --ink: #2b2b2b;
    --rule: #b9b9b9;
    --paper: #ffffff;
    --night: #111111;
    --night-soft: #262626;
    --stage: #e6e4e1;
  }
  * { box-sizing: border-box; margin: 0; padding: 0; }
  html, body { width: 1200px; height: 844px; overflow: hidden; }
  body {
    background: var(--stage);
    font-family: "Lato", Arial, sans-serif;
    position: relative;
  }
  .card {
    position: absolute;
    top: 270px;
    width: 500px;
    height: 303px;
    border-radius: 3px;
    box-shadow: 0 8px 24px rgba(0,0,0,.18);
    overflow: hidden;
  }
  /* Front */
  .card--front { left: 70px; background: var(--paper); color: var(--ink); }
  .brand-lockup {
    position: absolute; top: 34px; left: 150px;
    display: flex; align-items: center; gap: 10px;
  }
  .brand-dot { width: 40px; height: 40px; border-radius: 50%; background: var(--brand-blue); flex: none; }
  .brand-name {
    color: var(--brand-blue); font-weight: 700; font-size: 17px;
    line-height: 1.15; letter-spacing: .04em; text-transform: uppercase;
  }
  .write-rule { position: absolute; left: 250px; right: 30px; height: 1px; background: var(--rule); }
  .write-rule--1 { top: 100px; }
  .write-rule--2 { top: 132px; }
  .write-rule--3 { top: 164px; }
  .person { position: absolute; left: 30px; top: 172px; }
  .person-name { color: var(--brand-blue); font-weight: 700; font-size: 18px; letter-spacing: .02em; text-transform: uppercase; }
  .person-role { font-size: 13px; margin-top: 1px; }
  .contacts {
    position: absolute; left: 30px; top: 222px; right: 20px;
    display: grid; grid-template-columns: 170px 1fr; row-gap: 8px; column-gap: 10px;
    font-size: 12.5px;
  }
  .contact { display: flex; align-items: center; gap: 6px; white-space: nowrap; }
  .contact-icon { width: 15px; height: 15px; flex: none; }
  .social-dot { width: 15px; height: 15px; border-radius: 50%; background: var(--brand-blue); flex: none; }
  .appointment {
    position: absolute; left: 30px; right: 30px; bottom: 14px;
    display: flex; align-items: flex-end; gap: 6px;
    font-size: 12px; font-weight: 700; letter-spacing: .04em;
  }
  .appointment-line { flex: 1; border-bottom: 1px solid var(--ink); height: 12px; }
  /* Back */
  .card--back {
    left: 630px;
    background: radial-gradient(circle at 55% 35%, var(--night-soft), var(--night) 70%);
    color: var(--paper);
    display: flex; flex-direction: column; align-items: center; justify-content: center; gap: 18px;
  }
  .back-dot { width: 120px; height: 120px; border-radius: 50%; background: var(--paper); }
  .back-name {
    font-weight: 700; font-size: 17px; letter-spacing: .08em;
    text-transform: uppercase; text-align: center; line-height: 1.25;
  }
</style>
</head>
<body>
  <section class="card card--front" aria-label="Business card front">
    <div class="brand-lockup">
      <span class="brand-dot"></span>
      <span class="brand-name">The Harbourview<br>Motion Clinic</span>
    </div>
    <span class="write-rule write-rule--1"></span>
    <span class="write-rule write-rule--2"></span>
    <span class="write-rule write-rule--3"></span>

    <div class="person">
      <div class="person-name">Daniel Hart</div>
      <div class="person-role">Managing Director</div>
    </div>

    <div class="contacts">
      <div class="contact">
        <svg class="contact-icon" viewBox="0 0 16 16" aria-hidden="true">
          <circle cx="8" cy="8" r="7.2" fill="none" stroke="var(--brand-blue)" stroke-width="1.3"/>
          <path d="M5.3 4.3l1.3-.3.8 1.9-.9.7c.4.9 1.1 1.6 2 2l.7-.9 1.9.8-.3 1.3c-2.9.1-5.6-2.6-5.5-5.5z" fill="var(--brand-blue)"/>
        </svg>
        <span>402 718 3391</span>
      </div>
      <div class="contact">
        <svg class="contact-icon" viewBox="0 0 16 16" aria-hidden="true">
          <circle cx="8" cy="8" r="8" fill="var(--brand-blue)"/>
          <rect x="4" y="5.2" width="8" height="5.6" rx=".6" fill="none" stroke="#fff" stroke-width="1"/>
          <path d="M4.2 5.6L8 8.4l3.8-2.8" fill="none" stroke="#fff" stroke-width="1"/>
        </svg>
        <span>hello@harbourviewmotion.com</span>
      </div>
      <div class="contact">
        <span class="social-dot"></span>
        <span>/harbourviewmotionclinic</span>
      </div>
      <div class="contact">
        <span class="social-dot"></span>
        <span>@harbourviewmotionclinic</span>
      </div>
    </div>

    <div class="appointment">
      <span>DATE</span><span class="appointment-line"></span>
      <span>TIME</span><span class="appointment-line"></span>
    </div>
  </section>

  <section class="card card--back" aria-label="Business card back">
    <span class="back-dot"></span>
    <span class="back-name">The Harbourview<br>Motion Clinic</span>
  </section>
</body>
</html>
```